Web design for business website

I need a web design for a business website for one of our clients who is specialized in alarm management software. I would like you to design 3 web pages, one for each of the 3 pages. You need to process the corporate identity of our client to the web design. This means the colors of the logo (red and black) should definitely show up on all of the 3 pages. Find the logo file for the logo of our customer. To increase readability I suggest you use a white/light background. All suggestions are welcome.

Please kindly download atttached Webdesign.zip and read the project brief first. The project brief refers to all other files of the zip file. Your design must have exactly the same structure as the wireframes.
Updates

Target Market(s)

B2B, Alarm management

Industry/Entity Type

Business

Number of Pages Required

3 page

Requirements
Must have
• The web design must have exactly the same structure as the wireframes and needs to contain the colors of the company logo.

```html
<!DOCTYPE html>
<html lang="en">
<head>
<meta charset="utf-8">
<title>Corvex – Real-time reasoning solutions</title>
<link rel="stylesheet" href="https://fonts.googleapis.com/css2?family=Open+Sans:wght@400;600;700&family=Raleway:wght@400;600;700&display=swap">
<style>
:root{
  --orange:#e8471a;
  --navy:#1c1c3b;
  --ink:#222;
  --text:#555;
  --light:#f3f3f3;
  --dark:#121212;
  --darker:#0c0c0c;
  --line:#d8d8d8;
  --grey-btn:#d9d9d9;
}
*{box-sizing:border-box;margin:0;padding:0}
html,body{width:753px;height:1200px;overflow:hidden}
body{position:relative;font-family:"Open Sans",sans-serif;color:var(--text);background:#fff}
.abs{position:absolute}

.topbar{left:0;top:0;width:753px;height:21px;background:var(--dark);font-size:7px;color:#bbb}
.topbar .phone{left:62px;top:5px;display:flex;align-items:center;gap:5px}
.topbar .lang-label{left:480px;top:6px}
.topbar .lang-drop{left:541px;top:5px;width:15px;height:12px;background:var(--orange)}
.topbar .lang{left:557px;top:5px;width:36px;height:12px;background:#2a2a2a;text-align:center;line-height:12px}
.topbar .search{left:604px;top:5px;width:69px;height:12px;background:#2a2a2a;padding-left:7px;line-height:12px;font-size:5.5px;color:#999}
.topbar .search-btn{left:673px;top:5px;width:17px;height:12px;background:var(--orange)}

.header{left:0;top:21px;width:753px;height:54px;background:#f7f7f7}
.brand-name{left:62px;top:12px;font-family:"Open Sans",sans-serif;font-weight:600;font-size:22px;color:var(--ink);line-height:1}
.brand-tag{left:63px;top:38px;font-size:6px;color:var(--text)}
.hbtn{top:14px;height:27px;display:flex;align-items:center;font-size:6.5px;text-transform:uppercase}
.hbtn .ic{width:24px;height:100%;display:flex;align-items:center;justify-content:center;border-right:1px solid rgba(255,255,255,.35)}
.hbtn .lbl{flex:1;text-align:center}
.hbtn.account{left:454px;width:74px;background:var(--orange);color:#fff}
.hbtn.login{left:534px;width:75px;background:var(--grey-btn);color:#666}
.hbtn.signup{left:616px;width:74px;background:var(--grey-btn);color:#666}
.hbtn.login .ic,.hbtn.signup .ic{border-right-color:#aaa}

.nav{left:0;top:75px;width:753px;height:27px;background:var(--navy)}
.nav a{position:absolute;top:0;height:27px;line-height:27px;font-size:7px;color:#fff;text-decoration:none;text-transform:uppercase}
.nav a.active{background:var(--orange);font-weight:700;width:53px;text-align:center}

.hero{left:0;top:102px;width:753px;height:268px;background:linear-gradient(180deg,#8f8a7d 0%,#d7b582 35%,#c9a36a 55%,#5e6a3c 75%,#3d4a2a 100%)}
.hero-panel{left:207px;top:159px;width:339px;height:155px;background:rgba(235,235,235,.78)}
.hero-hello{left:230px;top:180px;font-size:12.5px;color:var(--ink)}
.hero-name{left:230px;top:191px;font-weight:700;font-size:32px;color:var(--orange);letter-spacing:.5px}
.hero-tag{left:388px;top:210px;font-size:9.5px;color:var(--ink)}
.hero-copy{left:233px;top:229px;width:270px;font-size:6.3px;line-height:9.6px;color:#444}
.btn{background:var(--orange);color:#fff;font-size:7px;font-weight:600;text-transform:uppercase;text-align:center;box-shadow:0 2px 0 #b8330f}
.hero-btn{left:231px;top:269px;width:86px;height:27px;line-height:27px}
.arrow{top:212px;width:32px;height:32px;display:flex;align-items:center;justify-content:center}
.arrow.prev{left:30px;background:#eee}
.arrow.next{left:691px;background:var(--orange)}

.about{left:0;top:370px;width:753px;height:270px;background:var(--light)}
.section-title{font-family:"Raleway",sans-serif;font-weight:700;color:var(--orange);text-align:center;width:753px;left:0}
.about-title{top:420px;font-size:19px}
.about-copy{left:118px;top:459px;width:517px;font-size:7.2px;line-height:10.8px;text-align:center;color:#555}
.about-copy p+p{margin-top:10.8px}
.about-btn{left:334px;top:571px;width:85px;height:27px;line-height:27px}

.clients-title{top:679px;font-size:15.5px}
.clients-rule{left:239px;top:700px;width:275px;height:1px;background:#ccc}
.clients-sub{left:0;top:709px;width:753px;text-align:center;font-family:"Raleway",sans-serif;font-size:9.6px;color:#666}
.client-band{left:0;top:748px;width:753px;height:55px;border-top:1px solid var(--line);border-bottom:1px solid var(--line)}
.client{position:absolute;top:0;height:53px;line-height:53px;font-weight:700;font-size:12px;color:#444;text-align:center}

.engage{left:0;top:850px;width:753px;height:134px;background:linear-gradient(180deg,#1a1d24 0%,#2a2c2e 45%,#3a3020 100%)}
.engage-title{font-family:"Raleway",sans-serif;font-weight:600;font-size:19.5px;color:var(--orange);top:883px}
.social{top:920px;width:26px;height:26px;background:#6e6e6e}
.social.first{background:#3b5a9a}
.sub-input{left:278px;top:921px;width:338px;height:25px;border:1px solid #fff;background:var(--darker);color:#fff;font-size:7px;line-height:23px;padding-left:14px}
.sub-btn{left:616px;top:921px;width:74px;height:25px;background:#fff;color:var(--orange);font-weight:700;font-size:7px;text-align:center;line-height:25px}

.footer{left:0;top:984px;width:753px;height:184px;background:var(--dark)}
.fcol{top:1026px}
.fcol h4{font-family:"Raleway",sans-serif;font-weight:400;font-size:9.5px;color:#444;margin-bottom:8px}
.fcol li{list-style:none;font-size:7.2px;line-height:12px;color:#555}
.fcol li.hl{color:var(--orange)}
.fcol .contact li{display:flex;align-items:center;gap:9px;line-height:17.5px}
.copy{left:0;top:1168px;width:753px;height:32px;background:var(--darker);border-top:1px solid #1e1e1e;text-align:center;line-height:31px;font-size:6px;color:#444}
.copy b{color:var(--orange);font-weight:400}
</style>
</head>
<body>

<div class="abs topbar">
  <div class="abs phone">
    <svg width="7" height="7" viewBox="0 0 10 10"><path d="M2 0l2 2-1 1.5c.8 1.6 2 2.8 3.5 3.5L8 6l2 2-1.5 2C4.5 10 0 5.5 0 1.5z" fill="#bbb"/></svg>
    <span>+00 (0)12 3456 789</span>
  </div>
  <div class="abs lang-label">Selecte Language :</div>
  <div class="abs lang-drop"><svg width="15" height="12"><path d="M5 4.5h5l-2.5 3z" fill="#fff"/></svg></div>
  <div class="abs lang">ENG</div>
  <div class="abs search">Search here...</div>
  <div class="abs search-btn"><svg width="17" height="12"><circle cx="8" cy="5.5" r="2.3" stroke="#fff" stroke-width="1.2" fill="none"/><path d="M9.7 7.2l1.8 1.8" stroke="#fff" stroke-width="1.3"/></svg></div>
</div>

<header class="abs header">
  <div class="abs brand-name">Corvex</div>
  <div class="abs brand-tag">Real-time reasoning solutions</div>
  <div class="abs hbtn account"><span class="ic"><svg width="8" height="8" viewBox="0 0 10 10"><circle cx="5" cy="3" r="2.4" fill="#fff"/><path d="M0.5 10c0-3 2-4.5 4.5-4.5S9.5 7 9.5 10z" fill="#fff"/></svg></span><span class="lbl">Account</span></div>
  <div class="abs hbtn login"><span class="ic"><svg width="8" height="8" viewBox="0 0 10 10"><rect x="1" y="4.5" width="6" height="5" fill="#666"/><path d="M5.5 4.5V3a2 2 0 0 1 4 0" stroke="#666" stroke-width="1.2" fill="none"/></svg></span><span class="lbl">Log in</span></div>
  <div class="abs hbtn signup"><span class="ic"><svg width="8" height="8" viewBox="0 0 10 10"><path d="M0 4h4V2l3 3-3 3V6H0z" fill="#666"/><path d="M6 1h3v8H6" stroke="#666" stroke-width="1" fill="none"/></svg></span><span class="lbl">Sign up</span></div>
</header>

<nav class="abs nav">
  <a class="active" style="left:62px">Home</a>
  <a style="left:140px">Industry</a>
  <a style="left:214px">Telecom</a>
  <a style="left:288px">Power</a>
  <a style="left:353px">Utilities</a>
  <a style="left:424px">Infra</a>
  <a style="left:484px">Store</a>
</nav>

<section class="abs hero" role="img" aria-label="Industrial refinery at sunset behind a grassy wetland"></section>
<div class="abs hero-panel"></div>
<div class="abs hero-hello">HELLO WE ARE</div>
<div class="abs hero-name">CORVEX</div>
<div class="abs hero-tag">Real-time reasoning solutions</div>
<p class="abs hero-copy">Companies have invested to get data out of processes. New technologies have been developed to get real-time data out of the harshest places, like oil-well drill heads or the Great Barrier Riff.</p>
<div class="abs btn hero-btn">Read more</div>
<div class="abs arrow prev"><svg width="8" height="8"><path d="M5 1.5L2.5 4 5 6.5" stroke="#e8471a" stroke-width="1.4" fill="none"/></svg></div>
<div class="abs arrow next"><svg width="8" height="8"><path d="M3 1.5L5.5 4 3 6.5" stroke="#fff" stroke-width="1.4" fill="none"/></svg></div>

<section class="abs about"></section>
<h2 class="abs section-title about-title">ABOUT US</h2>
<div class="abs about-copy">
  <p>Companies have invested to get data out of processes. New technologies have been developed to get real-time data out of the harshest places, like oil-well drill heads or the Great Barrier Riff. Data in itself means nothing without the context the data is collected in. Example: data from equipment under maintenance does not provide information to operations. Information - data which is valid and meaningful can overwhelm any user without the proper knowledge to interpret this information.</p>
  <p>Corvex technology enables easy application of such knowledge in a comprehensible – visual – representation and makes hypothetical reasoning with information possible providing meaningful advisories to subscribers when they need it or when it is required that they are made aware of a situation which requires their attention.</p>
</div>
<div class="abs btn about-btn">Learn more</div>

<h2 class="abs section-title clients-title">CLIENTS THAT TRUST US</h2>
<div class="abs clients-rule"></div>
<p class="abs clients-sub">Some of our clients that trust us, be shure to be one of them.</p>
<div class="abs client-band">
  <span class="client" style="left:82px;width:60px">Arvana</span>
  <span class="client" style="left:152px;width:90px">Keldmark</span>
  <span class="client" style="left:262px;width:50px">Solvio</span>
  <span class="client" style="left:344px;width:56px">Trenza</span>
  <span class="client" style="left:420px;width:88px">Brouwhal</span>
  <span class="client" style="left:530px;width:50px">Marlin</span>
  <span class="client" style="left:604px;width:82px">Halvrent</span>
</div>

<section class="abs engage" role="img" aria-label="Refinery at night, dimmed background"></section>
<h3 class="abs engage-title" style="left:62px">FOLLOW US ON :</h3>
<h3 class="abs engage-title" style="left:276px">SUBSCRIBE NOW :</h3>
<div class="abs social first" style="left:62px" aria-label="Social network"></div>
<div class="abs social" style="left:94px" aria-label="Social network"></div>
<div class="abs social" style="left:127px" aria-label="Social network"></div>
<div class="abs social" style="left:160px" aria-label="Social network"></div>
<div class="abs social" style="left:193px" aria-label="Social network"></div>
<div class="abs sub-input">Enter Your Email Adress</div>
<div class="abs sub-btn">SUBSCRIBE</div>

<footer class="abs footer"></footer>
<div class="abs fcol" style="left:62px"><h4>SOLUTIONS</h4><ul><li class="hl">KAM Alarm Reporting</li><li>KAM Alarm Analysis</li><li>KAM Alarm Expert</li><li>USE</li></ul></div>
<div class="abs fcol" style="left:170px"><h4>INDUSTRIES</h4><ul><li>Industry</li><li>Telecom</li><li>Power</li><li>Utilites</li><li>Infra</li></ul></div>
<div class="abs fcol" style="left:278px"><h4>ABOUT US</h4><ul><li>Company</li><li>Overview</li><li>Leadership</li><li>Partners</li><li>Locations</li></ul></div>
<div class="abs fcol" style="left:385px"><h4>NEWS</h4><ul><li>Product News</li><li>Partner News</li><li>Events</li><li>Press Releases</li><li>Vacancies</li></ul></div>
<div class="abs fcol" style="left:546px"><h4>CONTACT US</h4>
  <ul class="contact">
    <li><svg width="7" height="7" viewBox="0 0 10 10"><path d="M2 0l2 2-1 1.5c.8 1.6 2 2.8 3.5 3.5L8 6l2 2-1.5 2C4.5 10 0 5.5 0 1.5z" fill="#555"/></svg>+00 (0)12 3456 789</li>
    <li><svg width="7" height="6" viewBox="0 0 10 8"><rect width="10" height="8" fill="#555"/><path d="M0 0l5 4 5-4" stroke="#121212" fill="none"/></svg>hello@corvex.example</li>
    <li><svg width="6" height="8" viewBox="0 0 8 10"><path d="M4 10S0 5.5 0 4a4 4 0 0 1 8 0c0 1.5-4 6-4 6z" fill="#555"/><circle cx="4" cy="4" r="1.4" fill="#121212"/></svg>12 Harbour Lane, Eastport</li>
  </ul>
</div>
<div class="abs copy">Copyright © 2105 <b>CORVEX.</b> All Rights Reserved.</div>

</body>
</html>
```